Business card for a Exhibition booth fabrication company

Hi. My company would like to change our corporate name card. We are an events and Exhibition stand builder company. We would like our corporate name card to resonate what we do. I need someone to create something unique that relates to the industry that I am in. The graphic designer should be creative to incorporate the elements of my industry and try to blend in well in the design of the card. Our aim is to ensure that we are unique and our card can look different from our competitors.
Updates

Target Market(s)

Marketing and events manager from all companies

Contact Information for Business Card

The business card should have the following details:
Name
Job Title
Email
Website

Colors

Designer to choose colors to be used in the design.

Requirements
Must have
• The card must be look something that is relevant to the service that I am providing. My website is: www.velmora-buildworks.com
• You can see my website to get more information on what service that I am doing
Nice to have
• On the back of my card, I would like to have a globe image with the incorporation of my company logo. This is to indicate that my services can be done in any part of the world.

```html
<!DOCTYPE html>
<html lang="en">
<head>
<meta charset="utf-8">
<title>Velmora Buildworks — Business Card</title>
<link href="https://fonts.googleapis.com/css2?family=Jost:wght@400;500&family=Roboto:wght@400;500&display=swap" rel="stylesheet">
<style>
  :root {
    --stage: #3a3a3c;
    --card-dark: #0c0c0d;
    --card-dark-edge: #1b1b1d;
    --card-light: #f1f1f1;
    --brand-red: #e3101d;
    --ink: #111111;
    --wordmark-grey: #5b5b5b;
    --wordmark-light: #8a8a8a;
  }
  * { box-sizing: border-box; margin: 0; padding: 0; }
  html, body { width: 1200px; height: 1000px; overflow: hidden; }
  body {
    background: var(--stage);
    position: relative;
    font-family: "Jost", sans-serif;
  }
  .card {
    position: absolute;
    width: 700px;
    height: 400px;
    border-radius: 26px;
    overflow: hidden;
    box-shadow: 0 18px 40px rgba(0,0,0,0.35);
  }
  /* Back side */
  .card--back {
    left: 440px;
    top: 60px;
    background: radial-gradient(ellipse at 50% 45%, var(--card-dark-edge) 0%, var(--card-dark) 70%);
  }
  .world-map-area {
    position: absolute;
    left: 90px;
    top: 30px;
    width: 540px;
    height: 330px;
    border-radius: 40%;
    background: radial-gradient(ellipse at 50% 50%, rgba(90,90,95,0.35) 0%, rgba(40,40,42,0.15) 55%, rgba(12,12,13,0) 75%);
  }
  .back-brand {
    position: absolute;
    left: 0; right: 0;
    top: 172px;
    display: flex;
    align-items: center;
    justify-content: center;
    gap: 14px;
  }
  .back-brand .brand-dot {
    width: 22px; height: 22px; border-radius: 50%;
    background: var(--brand-red);
  }
  .back-brand .brand-name {
    font-weight: 500;
    font-size: 32px;
    letter-spacing: 3px;
    color: var(--wordmark-light);
  }
  /* Front side */
  .card--front {
    left: 60px;
    top: 540px;
    background: var(--card-light);
  }
  .front-brand {
    position: absolute;
    left: 46px;
    top: 58px;
    display: flex;
    align-items: center;
    gap: 12px;
  }
  .front-brand .brand-dot {
    width: 18px; height: 18px; border-radius: 50%;
    background: var(--brand-red);
  }
  .front-brand .brand-name {
    font-weight: 500;
    font-size: 24px;
    letter-spacing: 2.5px;
    color: var(--wordmark-grey);
  }
  .contact-block {
    position: absolute;
    left: 352px;
    top: 212px;
    color: var(--ink);
  }
  .person-name {
    font-family: "Roboto", sans-serif;
    font-weight: 500;
    font-size: 26px;
    color: var(--brand-red);
    line-height: 1.05;
  }
  .person-title {
    font-family: "Roboto", sans-serif;
    font-size: 16px;
    margin-bottom: 14px;
  }
  .contact-line {
    font-size: 16px;
    line-height: 1.45;
    display: flex;
    align-items: center;
    gap: 6px;
    white-space: nowrap;
  }
  .contact-label { color: var(--brand-red); }
  .contact-icon { width: 15px; height: 15px; flex: none; }
  .accent { color: var(--brand-red); }
</style>
</head>
<body>

<section class="card card--back" aria-label="Business card back">
  <div class="world-map-area" role="img" aria-label="Faint world map with connected network lines"></div>
  <div class="back-brand">
    <span class="brand-dot"></span>
    <span class="brand-name">VELMORA BUILDWORKS</span>
  </div>
</section>

<section class="card card--front" aria-label="Business card front">
  <div class="front-brand">
    <span class="brand-dot"></span>
    <span class="brand-name">VELMORA BUILDWORKS</span>
  </div>

  <div class="contact-block">
    <p class="person-name">Adrian Kell</p>
    <p class="person-title">President</p>
    <p class="contact-line"><span class="contact-label">Singapore Contact:</span> +65 91842706</p>
    <p class="contact-line"><span class="contact-label">Qatar Contact:</span> +974 70526184</p>
    <p class="contact-line">
      <svg class="contact-icon" viewBox="0 0 16 16" aria-hidden="true">
        <rect x="1" y="3" width="14" height="10" rx="1.5" fill="var(--brand-red)"/>
        <path d="M1.5 4 L8 9 L14.5 4" fill="none" stroke="#fff" stroke-width="1.3"/>
      </svg>
      info@velmora-buildworks.com
    </p>
    <p class="contact-line">
      <svg class="contact-icon" viewBox="0 0 16 16" aria-hidden="true">
        <circle cx="8" cy="8" r="7" fill="var(--brand-red)"/>
        <g fill="none" stroke="#fff" stroke-width="0.9">
          <ellipse cx="8" cy="8" rx="3" ry="7"/>
          <line x1="1" y1="8" x2="15" y2="8"/>
          <line x1="2.2" y1="4.5" x2="13.8" y2="4.5"/>
          <line x1="2.2" y1="11.5" x2="13.8" y2="11.5"/>
        </g>
      </svg>
      www.<span class="accent">velmora-buildworks</span>.com
    </p>
  </div>
</section>

</body>
</html>
```